Dunmore Roofing

Want a professional looking business card

Industry/Entity Type

Business

Contact Information for Business Card

Paul Dunmore ( Owner) paul@dunmoreroofing-example.com, www.dunmoreroofing-example.com, Adress: 4172 Township road 43 Plantagenet,ON K9X4T2

```html
<!DOCTYPE html>
<html lang="en">
<head>
<meta charset="utf-8">
<title>Dunmore Roofing – Business Card</title>
<link href="https://fonts.googleapis.com/css2?family=Montserrat:ital,wght@0,400;0,500;0,700;0,800;1,700&display=swap" rel="stylesheet">
<style>
  :root {
    --brand-blue: #1f4a8f;
    --brand-blue-deep: #1c3f86;
    --steel-grey: #8a8c90;
    --ink: #4a4a4a;
    --paper: #ffffff;
    --backdrop: #d9dadc;
  }
  * { margin: 0; padding: 0; box-sizing: border-box; }
  html, body { width: 1200px; height: 900px; overflow: hidden; }
  body {
    background: var(--backdrop);
    font-family: "Montserrat", sans-serif;
    position: relative;
  }
  .card {
    position: absolute;
    left: 250px;
    width: 700px;
    height: 400px;
    overflow: hidden;
    box-shadow: 0 6px 18px rgba(0,0,0,0.18);
  }

  /* Back side */
  .card--back {
    top: 30px;
    background: linear-gradient(180deg, var(--brand-blue) 0%, var(--brand-blue-deep) 100%);
    color: var(--paper);
  }
  .back-brand {
    position: absolute;
    top: 150px;
    left: 0; right: 0;
    display: flex;
    justify-content: center;
    align-items: center;
    gap: 14px;
  }
  .brand-square {
    width: 22px; height: 22px;
    background: var(--paper);
  }
  .back-brand .brand-name {
    font-weight: 800;
    font-size: 40px;
    letter-spacing: 3px;
    color: var(--paper);
  }
  .back-web {
    position: absolute;
    top: 320px; left: 0; right: 0;
    text-align: center;
    font-size: 14px;
    letter-spacing: 1px;
  }

  /* Front side */
  .card--front {
    top: 470px;
    background: var(--paper);
  }
  .front-brand {
    position: absolute;
    top: 62px;
    right: 48px;
    display: flex;
    align-items: center;
    gap: 10px;
  }
  .front-brand .brand-square {
    width: 18px; height: 18px;
    background: var(--brand-blue);
  }
  .front-brand .brand-name {
    font-weight: 800;
    font-size: 27px;
    letter-spacing: 2px;
    color: var(--brand-blue);
  }
  .name-tab {
    position: absolute;
    left: 50px; top: 118px;
    width: 12px; height: 40px;
    background: var(--brand-blue);
  }
  .person-name {
    position: absolute;
    left: 80px; top: 116px;
    font-weight: 700;
    font-style: italic;
    font-size: 22px;
    color: var(--brand-blue);
    letter-spacing: 0.5px;
  }
  .person-title {
    position: absolute;
    left: 80px; top: 145px;
    font-size: 13px;
    color: var(--ink);
    letter-spacing: 0.5px;
  }
  .divider {
    position: absolute;
    left: 80px; top: 176px;
    width: 575px; height: 2px;
    background: var(--brand-blue);
  }
  .contact-list {
    position: absolute;
    left: 70px; top: 196px;
    list-style: none;
    font-size: 14px;
    color: var(--ink);
    letter-spacing: 0.6px;
  }
  .contact-list li {
    display: flex;
    align-items: center;
    gap: 12px;
    height: 24px;
  }
  .contact-list svg { width: 14px; height: 14px; fill: var(--brand-blue); flex: none; }
  .contact-list .web-domain { color: var(--brand-blue); }
  .address {
    position: absolute;
    right: 55px; top: 236px;
    text-align: right;
    font-size: 15px;
    font-style: normal;
    line-height: 1.45;
    color: var(--ink);
    letter-spacing: 0.6px;
  }
  .front-footer {
    position: absolute;
    left: 0; bottom: 0;
    width: 700px; height: 60px;
  }
  .front-footer .stripe-grey { fill: var(--steel-grey); }
  .front-footer .band-blue { fill: var(--brand-blue); }
</style>
</head>
<body>

  <section class="card card--back" aria-label="Card back">
    <div class="back-brand">
      <span class="brand-square"></span>
      <span class="brand-name">DUNMORE ROOFING</span>
    </div>
    <p class="back-web">www.dunmoreroofing-example.com</p>
  </section>

  <section class="card card--front" aria-label="Card front">
    <div class="front-brand">
      <span class="brand-square"></span>
      <span class="brand-name">DUNMORE ROOFING</span>
    </div>

    <span class="name-tab"></span>
    <h1 class="person-name">PAUL DUNMORE</h1>
    <p class="person-title">OWNER</p>
    <span class="divider"></span>

    <ul class="contact-list">
      <li>
        <svg viewBox="0 0 24 24" aria-hidden="true"><path d="M6.6 10.8a15.1 15.1 0 0 0 6.6 6.6l2.2-2.2a1 1 0 0 1 1-.25 11.4 11.4 0 0 0 3.6.57 1 1 0 0 1 1 1V20a1 1 0 0 1-1 1A17 17 0 0 1 3 4a1 1 0 0 1 1-1h3.5a1 1 0 0 1 1 1c0 1.25.2 2.45.57 3.57a1 1 0 0 1-.25 1z"/></svg>
        <span>(000)123-4567</span>
      </li>
      <li>
        <svg viewBox="0 0 24 24" aria-hidden="true"><path d="M2 5h20v2l-10 6L2 7zM2 9l10 6 10-6v10H2z"/></svg>
        <span>paul@dunmoreroofing-example.com</span>
      </li>
      <li>
        <svg viewBox="0 0 24 24" aria-hidden="true"><path d="M12 2a10 10 0 1 0 0 20 10 10 0 0 0 0-20zm7.9 9h-3.4a15 15 0 0 0-1.3-6.2A8 8 0 0 1 19.9 11zM12 4c.9 1.2 2.3 3.7 2.5 7h-5C9.7 7.7 11.1 5.2 12 4zM8.8 4.8A15 15 0 0 0 7.5 11H4.1a8 8 0 0 1 4.7-6.2zM4.1 13h3.4a15 15 0 0 0 1.3 6.2A8 8 0 0 1 4.1 13zM12 20c-.9-1.2-2.3-3.7-2.5-7h5c-.2 3.3-1.6 5.8-2.5 7zm3.2-.8a15 15 0 0 0 1.3-6.2h3.4a8 8 0 0 1-4.7 6.2z"/></svg>
        <span>www.<span class="web-domain">dunmoreroofing-example</span>.com</span>
      </li>
    </ul>

    <address class="address">
      4172 Township<br>
      road 43 Ashford Falls,<br>
      KT K9X4T2
    </address>

    <svg class="front-footer" viewBox="0 0 700 60" preserveAspectRatio="none" aria-hidden="true">
      <path class="stripe-grey" d="M0 2 H395 Q405 2 412 9 H0 Z"/>
      <path class="band-blue" d="M0 18 H400 C425 18 430 2 462 2 H700 V60 H0 Z"/>
    </svg>
  </section>

</body>
</html>
```